Executive Business Card for Healthcare Company [Need Today]

I need a business card design for a healthcare company. The only branding the company has thus far is a logo. The cards will be utilized by company executives. The design I envision will be vibrant and appealing but with a corporate feel. They shouldn't be too casual or playful. I would like to complete this project TODAY if possible.

Target Market(s)

Healthcare vendors, other executives in healthcare and pharmaceuticals

Industry/Entity Type

Pharmaceutical

Contact Information for Business Card

See attachment

Font styles to use
Serif
Sans Serif

Colors

Designer to choose colors to be used in the design.

```html
<!DOCTYPE html>
<html lang="en">
<head>
<meta charset="utf-8">
<title>Corvane Therapeutics – Executive Business Card</title>
<link href="https://fonts.googleapis.com/css2?family=Lato:wght@300;400;700&display=swap" rel="stylesheet">
<style>
  :root {
    --backdrop: #ebe5d3;
    --card: #ffffff;
    --teal: #2bb8c8;
    --green: #5ec39a;
    --ink: #1e1e1e;
    --ink-soft: #444444;
    --divider: #9a9a9a;
  }
  * { box-sizing: border-box; margin: 0; padding: 0; }
  html, body {
    width: 1200px; height: 1200px; overflow: hidden;
    background: var(--backdrop);
    font-family: "Lato", sans-serif;
  }
  .canvas {
    position: relative; width: 1200px; height: 1200px;
  }
  .card {
    position: absolute; left: 180px; width: 840px; height: 480px;
    background: var(--card); overflow: hidden;
    box-shadow: 0 6px 18px rgba(0,0,0,0.12);
  }
  .card--front { top: 90px; }
  .card--back { top: 630px; }

  /* Front */
  .identity { position: absolute; left: 70px; top: 58px; color: var(--ink); }
  .identity__name { font-weight: 700; font-size: 30px; letter-spacing: 0.2px; }
  .identity__title { font-weight: 400; font-size: 21px; color: var(--ink-soft); margin-top: 4px; }
  .identity__company { font-weight: 700; font-size: 21px; margin-top: 2px; }

  .decor-circle {
    position: absolute; left: 30px; top: 250px;
    width: 350px; height: 350px; border-radius: 50%;
    border: 8px solid var(--green);
  }

  .contact-rule {
    position: absolute; left: 470px; top: 150px; width: 2px; height: 230px;
    background: var(--green);
  }
  .contact { position: absolute; left: 500px; top: 152px; list-style: none; color: var(--ink); }
  .contact__item {
    display: flex; align-items: center; gap: 12px;
    font-size: 21px; line-height: 31px;
  }
  .contact__item--gap { margin-top: 10px; }
  .contact__icon { width: 24px; height: 24px; flex: none; }
  .contact__address { font-weight: 700; font-size: 21px; line-height: 28px; margin-top: 14px; padding-left: 36px; }

  /* Back */
  .brand {
    position: absolute; inset: 0;
    display: flex; align-items: center; justify-content: center; gap: 30px;
  }
  .brand__circle {
    width: 190px; height: 190px; border-radius: 50%;
    border: 7px solid var(--green);
  }
  .brand__rule { width: 2px; height: 120px; background: var(--divider); }
  .brand__name {
    font-weight: 400; font-size: 52px; line-height: 1.05;
    color: var(--teal); letter-spacing: 0.5px;
  }
</style>
</head>
<body>
<main class="canvas">
  <section class="card card--front" aria-label="Business card front">
    <div class="identity">
      <p class="identity__name">Daniel Mercer</p>
      <p class="identity__title">Senior Director of Marketing</p>
      <p class="identity__company">Corvane Therapeutics, LLC</p>
    </div>

    <div class="decor-circle"></div>

    <div class="contact-rule"></div>
    <ul class="contact">
      <li class="contact__item">
        <svg class="contact__icon" viewBox="0 0 24 24"><circle cx="12" cy="12" r="12" fill="var(--teal)"/><rect x="8.5" y="5" width="7" height="14" rx="1.5" fill="#fff"/><rect x="9.8" y="7" width="4.4" height="8.5" fill="var(--teal)"/></svg>
        <span>555-210-4837</span>
      </li>
      <li class="contact__item">
        <svg class="contact__icon" viewBox="0 0 24 24"><circle cx="12" cy="12" r="12" fill="var(--teal)"/><path d="M6 10c0-2 3-3 6-3s6 1 6 3l-2 1-1.5-1.5h-5L8 11z" fill="#fff"/><rect x="7.5" y="12" width="9" height="5" rx="1" fill="#fff"/></svg>
        <span>555-390-1642</span>
      </li>
      <li class="contact__item contact__item--gap">
        <svg class="contact__icon" viewBox="0 0 24 24"><circle cx="12" cy="12" r="12" fill="var(--teal)"/><rect x="6" y="8" width="12" height="8.5" rx="1" fill="#fff"/><path d="M6.5 8.5l5.5 4.5 5.5-4.5" stroke="var(--teal)" stroke-width="1.4" fill="none"/></svg>
        <span>dmercer@corvanerx.com</span>
      </li>
      <li class="contact__item">
        <svg class="contact__icon" viewBox="0 0 24 24"><circle cx="12" cy="12" r="12" fill="var(--teal)"/><g stroke="#fff" stroke-width="1.4" fill="none"><circle cx="12" cy="12" r="6.5"/><ellipse cx="12" cy="12" rx="2.8" ry="6.5"/><path d="M5.5 12h13"/></g></svg>
        <span>www.corvanerx.com</span>
      </li>
      <li class="contact__address">118 Linden Avenue<br>Marlow, GA 30000</li>
    </ul>
  </section>

  <section class="card card--back" aria-label="Business card back">
    <div class="brand">
      <div class="brand__circle"></div>
      <div class="brand__rule"></div>
      <p class="brand__name">corvane<br>therapeutics</p>
    </div>
  </section>
</main>
</body>
</html>
```